KBT Business Cards

We require business cards for our business. We would like a matte black back to the card, with our logo centred in the middle. The front side of the card is open to design.

Target Market(s)

Clients looking for legal services (professional)

Industry/Entity Type

Legal

Contact Information for Business Card

Doran Kelbrath
Partner
Mobile: 0461 738 524
Email: doran@kbtlaw.co
Website: www.kbtlaw.co
Level 3, 118 Wendmore Street
Sydney NSW 2000

Font styles to use
Other font styles liked:
• Avenir

Colors
f04a50
ffffff
1b1b1b

Requirements
Must have
• Black back with logo included in the centre of the card.
• Our font is Avenir.

```html
<!DOCTYPE html>
<html lang="en">
<head>
<meta charset="utf-8">
<title>KBT Law Business Cards</title>
<link rel="stylesheet" href="https://fonts.googleapis.com/css2?family=Nunito+Sans:wght@400;700;800&display=swap">
<style>
  :root {
    --brand-red: #d6294a;
    --white: #ffffff;
    --card-black: #1b1b1b;
    --card-deep: #0e0e0e;
    --muted: #d8d8d8;
    --divider: #5a5a5a;
    --page: #d4d5d7;
  }
  * { box-sizing: border-box; margin: 0; padding: 0; }
  html, body { width: 1200px; height: 1090px; overflow: hidden; }
  body {
    background: var(--page);
    font-family: "Nunito Sans", sans-serif;
    position: relative;
  }
  .card {
    position: absolute;
    width: 758px;
    height: 434px;
    overflow: hidden;
    color: var(--white);
  }
  .card--front { left: 361px; top: 66px; }
  .card--back { left: 83px; top: 580px; }
  .card-surface {
    position: absolute; inset: 0;
    background: radial-gradient(ellipse at 45% 25%, #2e2e2e 0%, var(--card-black) 45%, var(--card-deep) 100%);
  }
  .brand {
    position: absolute;
    display: flex;
    align-items: center;
  }
  .brand-square { background: var(--brand-red); flex: none; }
  .brand-name {
    font-weight: 800;
    color: var(--white);
    line-height: 1;
    letter-spacing: 0.5px;
  }
  .card--front .brand { left: 70px; top: 175px; gap: 24px; }
  .card--front .brand-square { width: 64px; height: 64px; }
  .card--front .brand-name { font-size: 38px; }
  .divider {
    position: absolute; left: 388px; top: 98px;
    width: 1px; height: 237px; background: var(--divider);
  }
  .contact { position: absolute; left: 420px; top: 92px; }
  .contact-name {
    color: var(--brand-red); font-weight: 800; font-size: 24px;
    letter-spacing: 0.5px; line-height: 1.2;
  }
  .contact-role { font-size: 17px; color: var(--muted); letter-spacing: 0.5px; margin-top: 2px; }
  .contact-address { font-size: 19px; color: var(--muted); line-height: 29px; margin-top: 28px; }
  .contact-lines { list-style: none; margin-top: 22px; }
  .contact-lines li {
    display: flex; align-items: center; gap: 9px;
    font-size: 19px; color: var(--muted); height: 32px;
  }
  .contact-lines svg { width: 17px; height: 17px; flex: none; }
  .card--back .brand { left: 190px; top: 150px; gap: 34px; }
  .card--back .brand-square { width: 96px; height: 96px; }
  .card--back .brand-name { font-size: 52px; }
  .back-web {
    position: absolute; left: 0; right: 0; top: 380px;
    text-align: center; font-size: 19px; letter-spacing: 4px; color: var(--muted);
  }
  .back-web strong { color: var(--brand-red); font-weight: 700; }
</style>
</head>
<body>

<section class="card card--front" aria-label="Front of business card">
  <div class="card-surface" role="img" aria-label="Black leather texture"></div>
  <div class="brand">
    <span class="brand-square"></span>
    <span class="brand-name">KBT<br>LAW</span>
  </div>
  <div class="divider"></div>
  <div class="contact">
    <p class="contact-name">DORAN KELBRATH</p>
    <p class="contact-role">PARTNER</p>
    <p class="contact-address">Level 3, 118 Wendmore Street<br>Sydney NSW 2000</p>
    <ul class="contact-lines">
      <li>
        <svg viewBox="0 0 16 16" aria-hidden="true"><rect x="3" y="1" width="10" height="14" rx="2" fill="none" stroke="#d6294a" stroke-width="1.6"/><circle cx="8" cy="12" r="1" fill="#d6294a"/></svg>
        0461 738 524
      </li>
      <li>
        <svg viewBox="0 0 16 16" aria-hidden="true"><rect x="1" y="3" width="14" height="10" fill="#d6294a"/><path d="M1 3 L8 9 L15 3" fill="none" stroke="#1b1b1b" stroke-width="1.2"/></svg>
        doran@kbtlaw.co
      </li>
      <li>
        <svg viewBox="0 0 16 16" aria-hidden="true"><g fill="none" stroke="#d6294a" stroke-width="1.4"><circle cx="8" cy="8" r="6.5"/><ellipse cx="8" cy="8" rx="3" ry="6.5"/><line x1="1.5" y1="8" x2="14.5" y2="8"/></g></svg>
        www.kbtlaw.co
      </li>
    </ul>
  </div>
</section>

<section class="card card--back" aria-label="Back of business card">
  <div class="card-surface" role="img" aria-label="Black leather texture"></div>
  <div class="brand">
    <span class="brand-square"></span>
    <span class="brand-name">KBT<br>LAW</span>
  </div>
  <p class="back-web">www.<strong>kbtlaw</strong>.co</p>
</section>

</body>
</html>
```